Business Card Design - Photographer

I am a landscape photographer and I require a business card design. 

I require two designs:
1)  a double sided business card
 and
b)  a single sided business card 

The single sided design can either be the same as the double sided (with just one side having all the information)....or it can be an entire new design. Its up to you.

My corporate colours are (CMYK):

Blue   69, 32, 0, 0
Grey  72,  64,  47,  31
Green  32,  2,  91,  0
Yellow   0, 19, 92, 0
Orange  0, 39, 75, 0

Colour space in final file should be in CMYK.

The details that need to be included on the card:

- Use the provided Logo
- Name: Wiktor Baranowski
- Email:   sales@vistalumeworks.com.au
- Website:    vistalumeworks.com.au
- Twitter:    twitter.com/vistalumeworks
- Facebook:   facebook.com/vistalumeworks
- Mobile  0417 539 662

Please use the attached template to design the logo to the specified size, including the marked bleed lines. I have also attached my logo in PNG (transparent background) and ai format for you to use.

The final file should be:
- Photoshop version with layers so I can edit the name/text etc. All non vector files should be high resolution at 1039 x 697 pixels at 300 dpi.

I also require a file as:
- Vector based PDF

Anyway questions please contact me.

Thank you

Industry/Entity Type

Landscape

Logo styles of interest
Pictorial/Combination Logo
Abstract Logo
Wordmark Logo
Lettermark Logo
Requirements
Must have
• The details that need to be included on the card:

- Use the provided Logo
- Name: Wiktor Baranowski
- Email: sales@vistalumeworks.com.au
- Website: vistalumeworks.com.au
- Twitter: twitter.com/vistalumeworks
- Facebook: facebook.com/vistalumeworks
- Mobile 0417 539 662

```html
<!DOCTYPE html>
<html lang="en">
<head>
<meta charset="utf-8">
<title>Vistalume Works – Business Cards</title>
<link rel="stylesheet" href="https://fonts.googleapis.com/css2?family=Cinzel:wght@600&family=Source+Sans+3:wght@400;700&display=swap">
<style>
  :root {
    --backdrop: #2e3434;
    --card: #ffffff;
    --ink: #3a3d4d;
    --brand-blue: #3d8fcc;
    --brand-green: #b5d340;
    --brand-grey: #3a3d4d;
  }
  * { margin: 0; padding: 0; box-sizing: border-box; }
  html, body { width: 987px; height: 1200px; overflow: hidden; }
  body {
    position: relative;
    background: var(--backdrop);
    font-family: "Source Sans 3", "Myriad Pro", Arial, sans-serif;
    color: var(--ink);
  }
  .card {
    position: absolute;
    width: 790px;
    height: 451px;
    background: var(--card);
    border-radius: 26px;
    overflow: hidden;
  }
  .card--front { left: 96px; top: 110px; }
  .card--back  { left: 92px; top: 637px; }
  .card svg { position: absolute; inset: 0; }
  .wordmark { font-family: "Cinzel", "Trajan Pro", Georgia, serif; font-weight: 600; fill: var(--ink); }
  .tagline { font-family: "Cinzel", "Trajan Pro", Georgia, serif; font-weight: 600; fill: var(--ink); }
  .holder {
    position: absolute;
    left: 50px; top: 244px;
    font-size: 30px; font-weight: 700; line-height: 1;
    white-space: nowrap;
  }
  .holder .role { font-size: 19px; font-weight: 400; }
  .contacts {
    position: absolute;
    left: 50px; top: 302px;
    list-style: none;
    font-size: 17px; line-height: 24.4px;
  }
  .contacts b { font-weight: 700; }
  .web {
    position: absolute;
    left: 0; right: 0; top: 397px;
    text-align: center;
    font-size: 26px;
  }
</style>
</head>
<body>

<article class="card card--front" aria-label="Business card front">
  <svg width="790" height="451" viewBox="0 0 790 451">
    <path class="band-green" fill="var(--brand-green)"
      d="M632,0 C704,60 744,150 736,270 C728,360 676,410 620,451 L790,451 L790,0 Z"/>
    <path class="band-blue" fill="var(--brand-blue)" stroke="#fff" stroke-width="6"
      d="M428,454 C546,412 690,340 724,170 C738,250 730,320 708,366 C686,408 652,432 616,454 Z"/>
    <circle class="brand-dot" cx="229" cy="66" r="48" fill="var(--brand-grey)"/>
    <text class="wordmark" x="49" y="197" font-size="33" textLength="364" lengthAdjust="spacingAndGlyphs">VISTALUME WORKS</text>
    <text class="tagline" x="104" y="230" font-size="14" textLength="258" lengthAdjust="spacing">FINE ART PHOTOGRAPHY</text>
  </svg>
  <p class="holder">Your Name - <span class="role">Adminsitrator</span></p>
  <ul class="contacts">
    <li><b>m</b> : 0417 539 662</li>
    <li><b>e</b> : sales@vistalumeworks.com.au</li>
    <li><b>w</b> : vistalumeworks.com.au</li>
    <li><b>t</b> : twitter.com/vistalumeworks</li>
    <li><b>f</b> : facebook.com/vistalumeworks</li>
  </ul>
</article>

<article class="card card--back" aria-label="Business card back">
  <svg width="790" height="451" viewBox="0 0 790 451">
    <circle class="brand-dot" cx="393" cy="128" r="70" fill="var(--brand-grey)"/>
    <text class="wordmark" x="111" y="308" font-size="52" textLength="564" lengthAdjust="spacingAndGlyphs">VISTALUME WORKS</text>
    <text class="tagline" x="192" y="358" font-size="22" textLength="402" lengthAdjust="spacing">FINE ART PHOTOGRAPHY</text>
  </svg>
  <p class="web">www.vistalumeworks.com.au</p>
</article>

</body>
</html>
```